Business card for law firm

Need business card for new law firm. Think confident, authoritative, conservative, but not stuffy or old-fashioned.

Contact Information for Business Card

Content for card - logo (uploaded), plus the following:

Paul Whitcombe (larger font)
Managing Partner (larger font, but not as large as name)
Level 9, 7 Ferris Lane
Sydney NSW 2000
Main Tel 02 9364 2710
Direct Tel 02 8472 3159
Email paul@qvlegal.com.au
www.qvlegal.com.au

Letterhead design should include logo plus:
Level 9, 7 Ferris Lane
Sydney NSW 2000
Tel 02 8472 3159
www.qvlegal.com.au

```html
<!DOCTYPE html>
<html lang="en">
<head>
<meta charset="utf-8">
<title>Quayvale Legal — Letterhead</title>
<link rel="stylesheet" href="https://fonts.googleapis.com/css2?family=Questrial&family=Tinos&display=swap">
<style>
  :root {
    --navy: #0b1f5c;
    --canvas: #e2e2e2;
    --paper-light: #f3f3f3;
    --paper-dark: #e3e3e3;
    --text: #6e6e6e;
    --text-soft: #7c7c7c;
    --brand: #4a4a4a;
    --ink: #2f5fb0;
  }
  * { box-sizing: border-box; margin: 0; padding: 0; }
  html, body { width: 1024px; height: 1200px; overflow: hidden; background: var(--canvas); }
  .letterhead {
    position: absolute; left: 102px; top: 25px;
    width: 820px; height: 1150px;
    background: var(--navy);
  }
  .sheet {
    position: absolute; inset: 0;
    background: linear-gradient(100deg, var(--paper-light) 0%, var(--paper-dark) 100%);
    border-top-right-radius: 146px 188px;
    border-bottom-left-radius: 194px 185px;
    font-family: "Questrial", sans-serif;
    color: var(--text);
  }
  .brand {
    position: absolute; left: 70px; top: 78px;
    display: flex; align-items: center; gap: 12px;
  }
  .brand-mark { width: 26px; height: 26px; background: var(--navy); }
  .brand-name {
    font-size: 21px; letter-spacing: 2px; text-transform: uppercase;
    color: var(--brand);
  }
  .salutation {
    position: absolute; left: 77px; top: 300px;
    font-size: 20px; color: var(--text-soft);
  }
  .body-copy {
    position: absolute; left: 77px; top: 362px; width: 680px;
    font-size: 11.6px; line-height: 13.8px; text-align: justify;
  }
  .body-copy p + p { margin-top: 14px; }
  .closing {
    position: absolute; left: 77px; top: 731px; font-size: 11.6px;
  }
  .signature {
    position: absolute; left: 77px; top: 800px; width: 145px; height: 64px;
    background: linear-gradient(90deg, rgba(47,95,176,0.18), rgba(47,95,176,0.06));
    border-radius: 6px;
  }
  .contact {
    position: absolute; right: 65px; top: 1020px;
    font-family: "Tinos", serif; font-size: 14.5px; line-height: 20px;
    color: var(--navy); text-align: right;
  }
  .contact-line { display: flex; justify-content: flex-end; align-items: center; gap: 6px; }
  .contact-line svg { width: 12px; height: 12px; fill: var(--navy); }
</style>
</head>
<body>
  <div class="letterhead">
    <div class="sheet">
      <div class="brand">
        <span class="brand-mark"></span>
        <span class="brand-name">Quayvale Legal</span>
      </div>

      <p class="salutation">Dear Mr. Hollis,</p>

      <div class="body-copy">
        <p>Lorem ipsum dolor sit amet, consectetur adipiscing elit. Donec orci purus, luctus vitae dignissim eu, iaculis sed purus. Vivamus faucibus, ipsum nec aliquet viverra, leo mauris condimentum ligula, sit amet sagittis enim ligula quis arcu. Nam egestas tortor id nisi porttitor mattis. In tortor ante, ultricies in suscipit a, tempus non massa. Vivamus et auctor mi. Fusce vel massa nulla. Phasellus nec eros mauris, et scelerisque orci.</p>
        <p>Donec malesuada orci vitae nulla accumsan porta a id massa. Quisque accumsan iaculis magna sit amet fringilla. Maecenas consequat, magna eget tincidunt semper, odio nibh rutrum mi, id feugiat ante nisi eu risus. Vestibulum nunc orci, rhoncus a placerat in, ultricies in mi. Cras mattis varius eros, vel fringilla nisi suscipit eget. Quisque scelerisque sagittis nulla at porttitor.</p>
        <p>Sed id augue vitae urna euismod commodo aliquet a quam. Pellentesque arcu velit, cursus et malesuada ut, consequat et diam. Nullam erat sem, rhoncus id ullamcorper vitae, rhoncus et arcu. In ultricies ultricies nulla, ut rutrum nisi iaculis at. Donec eu magna a metus ornare faucibus. Fusce aliquet faucibus ultricies. Morbi semper, est id tincidunt gravida, sem arcu adipiscing lacus, ac bibendum nulla leo eu purus. Quisque nec diam sed risus consectetur accumsan quis quis nibh. Vestibulum id purus lorem.</p>
        <p>It is a long established fact that a reader will be distracted by the readable content of a page when looking at its layout. The point of using Lorem Ipsum is that it has a more-or-less normal distribution of letters, as opposed to using 'Content here, content here', making it look like readable English. Many desktop publishing packages</p>
      </div>

      <p class="closing">Sincerely,</p>

      <div class="signature" role="img" aria-label="Handwritten signature of James Hollis in blue ink"></div>

      <address class="contact" style="font-style: normal;">
        <div class="contact-line">Level 9, 7 Ferris Lane</div>
        <div class="contact-line">Sydney NSW 2000</div>
        <div class="contact-line">02 8472 3159
          <svg viewBox="0 0 24 24" aria-hidden="true"><path d="M6.6 10.8a15.1 15.1 0 0 0 6.6 6.6l2.2-2.2c.3-.3.7-.4 1-.2 1.1.4 2.3.6 3.6.6.6 0 1 .4 1 1V20c0 .6-.4 1-1 1A17 17 0 0 1 3 4c0-.6.4-1 1-1h3.5c.6 0 1 .4 1 1 0 1.3.2 2.5.6 3.6.1.3 0 .7-.2 1z"/></svg>
        </div>
        <div class="contact-line">www.qvlegal.com.au
          <svg viewBox="0 0 24 24" aria-hidden="true"><circle cx="12" cy="12" r="11"/><path d="M12 1v22M1 12h22" stroke="#f0f0f0" stroke-width="1.6" fill="none"/><ellipse cx="12" cy="12" rx="5" ry="11" stroke="#f0f0f0" stroke-width="1.6" fill="none"/></svg>
        </div>
      </address>
    </div>
  </div>
</body>
</html>
```